New Business Card for our Indoor Golf Training Facility

We are looking for designs for a new business card for our indoor golf training facility. Attached is our logo, our logo with our slogan, and here is our elevator pitch (What makes us different from the others) not sure if all the info will fit on one card, maybe you can condense the elevator pitch? here is the info

Elevator Pitch
We work with serious golfers and those that want to be serious golfers…
to make you better, faster, at all phases of the game…
We use the same state-of-the-art technology as professional golfers…
which produces data sets that shows your improvement in real time.
Our facility is available 24/7 to our members, which allows you to improve on your time.

our website: www.birchpinlinks.com

Target Market(s)

Golfers

Font styles to use
Serif
Sans Serif

Colors
ec1f27
f59195
fbd4d5
919191
d3d3d3
1b1b1b

Requirements
Must have
• our logo or our logo with the slogan, elevator pitch (can be condensed or shortened)

```html
<!DOCTYPE html>
<html lang="en">
<head>
<meta charset="utf-8">
<title>Birch Pin Links – Business Card</title>
<link rel="stylesheet" href="https://fonts.googleapis.com/css2?family=Roboto:wght@400;500&family=Work+Sans:wght@400;500;800&display=swap">
<style>
  :root {
    --brand-red: #ec3a35;
    --ink: #1b1b1b;
    --ink-soft: #333333;
    --paper: #ffffff;
    --backdrop: #d3d3d3;
  }
  * { box-sizing: border-box; margin: 0; padding: 0; }
  html, body { width: 1200px; height: 930px; overflow: hidden; }
  body {
    background: var(--backdrop);
    font-family: "Work Sans", Arial, sans-serif;
    position: relative;
  }
  .card {
    position: absolute;
    left: 250px;
    width: 700px;
    height: 400px;
    border-radius: 22px;
    overflow: hidden;
  }
  .card--front { top: 45px; background: var(--brand-red); color: var(--paper); }
  .card--back { top: 485px; background: var(--paper); color: var(--ink); }

  .brand__name {
    font-weight: 800; font-size: 52px; line-height: 1; letter-spacing: -0.5px;
  }
  .brand__tagline {
    font-weight: 400; font-size: 17px; margin-top: 6px; letter-spacing: 0.3px;
  }

  .card--front .brand {
    position: absolute; left: 0; right: 0; top: 62px; text-align: center;
  }

  .pitch {
    position: absolute; left: 40px; right: 40px; top: 190px;
    text-align: center; font-family: "Roboto", Arial, sans-serif;
  }
  .pitch__title { font-weight: 500; font-size: 20px; margin-bottom: 10px; }
  .pitch__line { font-size: 14.5px; line-height: 1.55; }

  .card--back .brand {
    position: absolute; right: 46px; top: 40px; text-align: right;
    color: var(--brand-red);
  }
  .card--back .brand__name { font-size: 38px; }
  .card--back .brand__tagline { font-size: 13px; margin-top: 4px; }

  .person { position: absolute; left: 70px; top: 206px; }
  .person__name { color: var(--brand-red); font-weight: 500; font-size: 36px; line-height: 1.05; }
  .person__role { color: var(--ink-soft); font-size: 18px; margin-top: 2px; }

  .address {
    position: absolute; right: 46px; top: 206px; text-align: right;
    font-size: 18px; line-height: 1.35; color: var(--ink-soft); font-style: normal;
  }
  .divider {
    position: absolute; left: 70px; right: 46px; top: 284px;
    height: 2px; background: var(--brand-red);
  }
  .contact { position: absolute; left: 96px; top: 298px; list-style: none; }
  .contact__item {
    display: flex; align-items: center; gap: 10px;
    font-size: 17px; line-height: 24px; color: var(--ink-soft);
  }
  .contact__icon { width: 14px; height: 14px; flex: none; }
  .contact__accent { color: var(--brand-red); }
</style>
</head>
<body>

<section class="card card--front">
  <div class="brand">
    <div class="brand__name">Birch Pin Links</div>
    <div class="brand__tagline">Train Smarter. Play Lower. Every Season.</div>
  </div>
  <div class="pitch">
    <h2 class="pitch__title">Elevator Pitch</h2>
    <p class="pitch__line">We work with serious golfers and those that want to be serious golfers…</p>
    <p class="pitch__line">to make you better, faster, at all phases of the game…</p>
    <p class="pitch__line">We use the same state-of-the-art technology as professional golfers…</p>
    <p class="pitch__line">which produces data sets that shows your improvement in real time.</p>
    <p class="pitch__line">Our facility is available 24/7 to our members, which allows you to improve on your time.</p>
  </div>
</section>

<section class="card card--back">
  <div class="brand">
    <div class="brand__name">Birch Pin Links</div>
    <div class="brand__tagline">Train Smarter. Play Lower. Every Season.</div>
  </div>

  <div class="person">
    <div class="person__name">Daniel Hartwell</div>
    <div class="person__role">Director</div>
  </div>

  <address class="address">
    1840 W. Alder Rd. Unit B4<br>
    Millbrook, OH 45000
  </address>

  <div class="divider"></div>

  <ul class="contact">
    <li class="contact__item">
      <svg class="contact__icon" viewBox="0 0 24 24"><path fill="#ec3a35" d="M6.6 10.8a15.2 15.2 0 0 0 6.6 6.6l2.2-2.2a1 1 0 0 1 1-.25 11.4 11.4 0 0 0 3.6.57 1 1 0 0 1 1 1V20a1 1 0 0 1-1 1A17 17 0 0 1 3 4a1 1 0 0 1 1-1h3.5a1 1 0 0 1 1 1c0 1.25.2 2.45.57 3.57a1 1 0 0 1-.25 1z"/></svg>
      555-310-2280
    </li>
    <li class="contact__item">
      <svg class="contact__icon" viewBox="0 0 24 24"><rect x="3" y="5" width="18" height="14" rx="1.5" fill="none" stroke="#ec3a35" stroke-width="2.4"/><path d="M3.5 6l8.5 7 8.5-7" fill="none" stroke="#ec3a35" stroke-width="2.4"/></svg>
      info@birchpinlinks.com
    </li>
    <li class="contact__item">
      <svg class="contact__icon" viewBox="0 0 24 24"><circle cx="12" cy="12" r="9" fill="none" stroke="#ec3a35" stroke-width="2.4"/><path d="M3 12h18M12 3c3 3 3 15 0 18M12 3c-3 3-3 15 0 18" fill="none" stroke="#ec3a35" stroke-width="2"/></svg>
      <span>www.<span class="contact__accent">birchpinlinks</span>.com</span>
    </li>
  </ul>
</section>

</body>
</html>
```